Four in One (Flexible infographic for Content Management Industry)

See attachment.
A graphic depicting 4 products, where each can stand on its own and each can be combined with others, but where, if all are taken together, the best result is achieved (the "super product").
Intended use is web. See attached file as an example.
The most basic idea is as the attached diagram shows, where 4 rectangles are arranged in a quadrangle, with a middle rectangle in the center representing the combined 4 products. This concept is fine except it is a bit too obvious as it stands. We are looking for either a variation of this or another concept.
The audience is technical + professional + enterprise - NOT consumers. Hence the design should be conservative in nature.
We are aware of tools like as Canva or Pictogram where such graphics are available, but we are looking for something with a bit more imagination and flexibility.
This graphic should be targeted to web sites and be delivered with vector-based (SVG) graphics.

```html
<!DOCTYPE html>
<html lang="en">
<head>
<meta charset="utf-8">
<title>Super Product – Four in One</title>
<link rel="stylesheet" href="https://fonts.googleapis.com/css2?family=Montserrat:wght@500;600;700;800&display=swap">
<style>
  :root {
    --docs-blue: #3c5e96;
    --security-slate: #53668b;
    --erp-teal: #4581ad;
    --digital-sky: #7b98b8;
    --ring-grey: #e6e7e8;
    --core-white: #ffffff;
    --ink-navy: #2e3b55;
    --frame-grey: #3a3a3a;
    --text-white: #ffffff;
  }
  * { margin: 0; padding: 0; box-sizing: border-box; }
  html, body { width: 1162px; height: 1200px; overflow: hidden; background: #fff; }
  body { font-family: "Montserrat", Arial, sans-serif; color: var(--text-white); }

  .canvas {
    position: relative;
    width: 1162px;
    height: 1200px;
    border: 1px solid var(--frame-grey);
    overflow: hidden;
  }

  .tile {
    position: absolute;
    width: 395px;
    height: 450px;
  }
  .tile--docs     { left: 164px; top: 133px; background: var(--docs-blue);     border-radius: 200px 50px 50px 40px; }
  .tile--security { left: 602px; top: 133px; background: var(--security-slate); border-radius: 50px 200px 40px 50px; }
  .tile--erp      { left: 164px; top: 617px; background: var(--erp-teal);      border-radius: 40px 50px 50px 200px; }
  .tile--digital  { left: 602px; top: 617px; background: var(--digital-sky);   border-radius: 50px 40px 200px 50px; }

  .abs { position: absolute; }

  .title { font-weight: 700; white-space: nowrap; }
  .rule { position: absolute; height: 2px; background: var(--text-white); }
  .summary { font-weight: 600; white-space: nowrap; }

  .checklist { list-style: none; font-weight: 600; white-space: nowrap; }
  .checklist li { position: relative; }
  .checklist li::before {
    content: "";
    position: absolute;
    width: 4px;
    height: 8px;
    border-right: 2px solid var(--text-white);
    border-bottom: 2px solid var(--text-white);
    transform: rotate(40deg);
  }

  /* Document Management */
  .docs-title { right: 725px; top: 175px; font-size: 28px; line-height: 34px; text-align: right; }
  .docs-icon { left: 461px; top: 180px; width: 38px; height: 52px; }
  .docs-rule { left: 218px; top: 282px; width: 304px; }
  .docs-summary { left: 185px; top: 306px; font-size: 14.6px; line-height: 21px; font-weight: 500; }
  .docs-list { left: 186px; top: 385px; font-size: 14.6px; line-height: 18.6px; font-weight: 500; }
  .docs-list li { padding-left: 18px; }
  .docs-list li::before { left: 2px; top: 5px; }

  /* Security and Compliance */
  .security-icon { left: 652px; top: 174px; width: 48px; height: 58px; }
  .security-title { left: 719px; top: 171px; font-size: 25.5px; line-height: 31px; }
  .security-rule { left: 645px; top: 282px; width: 304px; }
  .security-summary { left: 626px; top: 300px; font-size: 12.2px; line-height: 15.6px; }
  .security-list { left: 742px; top: 391px; font-size: 12.2px; line-height: 15.8px; }
  .security-list li { padding-left: 26px; }
  .security-list li::before { left: 3px; top: 3px; }

  /* Enterprise Resource Planning */
  .erp-icon { left: 200px; top: 659px; width: 47px; height: 53px; }
  .erp-title { right: 770px; top: 698px; font-size: 21.5px; line-height: 25.5px; text-align: right; }
  .erp-rule { left: 218px; top: 787px; width: 249px; }
  .erp-summary { right: 639px; top: 814px; font-size: 12.2px; line-height: 16px; text-align: right; }
  .erp-list { left: 227px; top: 892px; font-size: 12.2px; line-height: 15.8px; }
  .erp-list li { padding-left: 19px; }
  .erp-list li::before { left: 3px; top: 3px; }

  /* Digital Transformation */
  .digital-icon { left: 903px; top: 665px; width: 56px; height: 47px; }
  .digital-title { left: 786px; top: 697px; font-size: 23px; line-height: 28px; }
  .digital-rule { left: 692px; top: 787px; width: 256px; }
  .digital-summary { left: 648px; top: 814px; font-size: 12.2px; line-height: 16px; }
  .digital-list { left: 652px; top: 892px; font-size: 12.2px; line-height: 15.8px; }
  .digital-list li { padding-left: 26px; }
  .digital-list li::before { left: 3px; top: 3px; }

  /* Central hub */
  .hub-ring {
    position: absolute;
    left: 385px; top: 405px;
    width: 392px; height: 392px;
    border-radius: 50%;
    background: var(--ring-grey);
  }
  .hub-core {
    position: absolute;
    left: 427px; top: 447px;
    width: 308px; height: 308px;
    border-radius: 50%;
    background: var(--core-white);
  }
  .hub-name {
    position: absolute;
    left: 385px; top: 529px;
    width: 378px;
    text-align: center;
    color: var(--ink-navy);
    font-weight: 800;
    font-size: 57px;
    line-height: 51px;
    letter-spacing: -0.5px;
  }
</style>
</head>
<body>
<main class="canvas">

  <section class="tile tile--docs" aria-label="Document Management"></section>
  <section class="tile tile--security" aria-label="Security and Compliance"></section>
  <section class="tile tile--erp" aria-label="Enterprise Resource Planning"></section>
  <section class="tile tile--digital" aria-label="Digital Transformation"></section>

  <!-- Document Management -->
  <h2 class="abs title docs-title">Document<br>Management</h2>
  <svg class="abs docs-icon" viewBox="0 0 38 52" fill="none" stroke="#fff" stroke-width="2" aria-hidden="true">
    <path d="M2 2 H29 L36 9 V50 H2 Z"/>
    <path d="M29 2 V9 H36"/>
    <path d="M8 16 H30 M8 22 H30 M8 28 H30 M8 34 H30 M8 40 H30"/>
  </svg>
  <div class="rule docs-rule"></div>
  <p class="abs summary docs-summary">Streamline document organization, access, and<br>collaboration with easier file storage and sharing,<br>leading to more efficient workflows .</p>
  <ul class="abs checklist docs-list">
    <li>Centralized Document Control</li>
    <li>Collaborative Workspace Integration</li>
    <li>Automated Compliance Tracking</li>
    <li>Check 4</li>
  </ul>

  <!-- Security and Compliance -->
  <svg class="abs security-icon" viewBox="0 0 48 58" fill="none" stroke="#fff" stroke-width="3.5" stroke-linejoin="round" aria-hidden="true">
    <path d="M24 3 L45 11 V28 C45 42 35 51 24 55 C13 51 3 42 3 28 V11 Z"/>
    <path d="M14 29 L21 36 L35 21" stroke-linecap="round"/>
  </svg>
  <h2 class="abs title security-title">Security<br>and Compliance</h2>
  <div class="rule security-rule"></div>
  <p class="abs summary security-summary">Benefit from tailored cloud solutions, secure data<br>storage, and expert disaster recovery planning for<br>reliable and scalable IT operations.</p>
  <ul class="abs checklist security-list">
    <li>Custom Cloud Solutions</li>
    <li>Secure Data Storage</li>
    <li>Expert Disaster Recovery</li>
    <li>Check 4</li>
  </ul>

  <!-- Enterprise Resource Planning -->
  <svg class="abs erp-icon" viewBox="0 0 47 53" fill="none" stroke="#fff" stroke-width="2.5" aria-hidden="true">
    <path d="M9 9 H45 V51 H9 Z"/>
    <path d="M2 2 H38 V44 H2 Z" fill="var(--erp-teal)"/>
    <path d="M8 11 H30 M8 17 H30 M8 23 H30 M8 29 H30 M8 35 H30"/>
  </svg>
  <h2 class="abs title erp-title">Enterprise<br>Resource Planning</h2>
  <div class="rule erp-rule"></div>
  <p class="abs summary erp-summary">Simplify management across finance, sales, and<br>operations, enabling better decision-making<br>and improved productivity.</p>
  <ul class="abs checklist erp-list">
    <li>Integrated Business Processes</li>
    <li>Enhanced Decision-Making</li>
    <li>Productivity Improvement</li>
    <li>Check 4</li>
  </ul>

  <!-- Digital Transformation -->
  <svg class="abs digital-icon" viewBox="0 0 56 47" fill="none" stroke="#fff" stroke-width="5" stroke-linecap="round" aria-hidden="true">
    <path d="M4 15 C18 2 38 2 52 15"/>
    <path d="M12 23 C22 14 34 14 44 23"/>
    <path d="M20 31 C25 27 31 27 36 31"/>
    <circle cx="28" cy="40" r="5" fill="#fff" stroke="none"/>
  </svg>
  <h2 class="abs title digital-title">Digital<br>Transformation</h2>
  <div class="rule digital-rule"></div>
  <p class="abs summary digital-summary">Turn scanned documents into easily searchable<br>digital archives, boosting efficiency and<br>accessibility.</p>
  <ul class="abs checklist digital-list">
    <li>Instant searchable Archives with OCR</li>
    <li>Automated Document Classification</li>
    <li>DocuHub and Cloud Blob Ready</li>
    <li>Check 4</li>
  </ul>

  <!-- Central hub -->
  <div class="hub-ring"></div>
  <div class="hub-core"></div>
  <h1 class="hub-name">Super<br>Product</h1>

</main>
</body>
</html>
```